Florida-based Coastal Landscaping Company Needs Letterhead Designs

We are a newly established Florida-based, coastal landscaping company that is looking for some really innovative flyers that we can use to get our name our to affluent consumers that live on the coast of Florida (think on the beach) and small to medium sized businesses in the same area. We will be handing out 100s of thousands of these, so need a great design

Target Market(s)

Affluent consumers and small to medium sized businesses

Industry/Entity Type

It Company

Font styles to use
Sans Serif

Colors

Designer to choose colors to be used in the design.

Requirements
Must have
• Need to have company name, logo, individual name, phone number and contact info
Nice to have
• Florida - looking, island looking / paradise, but needs to focus on the landscaping elements
Should not have
• Regular generic lawn company letterhead designs. We are a top tier landscape design / build plus maintenance firm, so not your mom and pop lawn mowing company

```html
<!DOCTYPE html>
<html lang="en">
<head>
<meta charset="utf-8">
<title>Tidewater Gardens Letterhead</title>
<link rel="stylesheet" href="https://fonts.googleapis.com/css2?family=Open+Sans:wght@400;600&display=swap">
<style>
  :root {
    --backdrop: #c4ecf7;
    --paper: #ffffff;
    --ocean: #1fb0d8;
    --ocean-deep: #0f9cc8;
    --ocean-pale: #e3f5fb;
    --silver: #a9a9a9;
    --ink: #1d1d1d;
    --ink-soft: #5a5a5a;
  }
  html, body {
    margin: 0;
    padding: 0;
    width: 1200px;
    height: 784px;
    overflow: hidden;
    background: var(--backdrop);
    font-family: "Open Sans", Arial, sans-serif;
  }
  .canvas {
    position: relative;
    width: 1200px;
    height: 784px;
  }
  .letterhead {
    position: absolute;
    left: 314px;
    top: 22px;
    width: 572px;
    height: 740px;
    background: var(--paper);
    overflow: hidden;
    box-shadow: 0 2px 10px rgba(15, 120, 160, 0.18);
  }
  .letterhead-art {
    position: absolute;
    inset: 0;
    width: 572px;
    height: 740px;
  }
  .brand {
    position: absolute;
    left: 34px;
    top: 34px;
    display: flex;
    align-items: center;
    gap: 8px;
  }
  .brand-dot {
    width: 12px;
    height: 12px;
    border-radius: 50%;
    background: var(--ocean);
  }
  .brand-name {
    font-size: 20px;
    font-weight: 600;
    letter-spacing: 1.5px;
    color: var(--ocean-deep);
    text-transform: uppercase;
  }
  .contact {
    position: absolute;
    right: 34px;
    top: 36px;
    margin: 0;
    padding: 0;
    list-style: none;
    font-size: 8.5px;
    line-height: 12px;
    color: var(--ink-soft);
  }
  .contact li {
    display: flex;
    align-items: center;
    gap: 5px;
  }
  .contact .icon {
    width: 7px;
    height: 7px;
    border-radius: 50%;
    background: var(--ocean);
    flex: none;
  }
  .contact .indent { padding-left: 12px; }
</style>
</head>
<body>
<main class="canvas">
  <section class="letterhead">
    <svg class="letterhead-art" viewBox="0 0 572 740" aria-hidden="true">
      <defs>
        <linearGradient id="oceanFill" x1="0" y1="0" x2="1" y2="1">
          <stop offset="0" stop-color="#0d9cc8"/>
          <stop offset="1" stop-color="#5fd0ec"/>
        </linearGradient>
      </defs>
      <path class="middle-wave" d="M0 300 C 150 290, 260 330, 290 390 C 320 450, 420 470, 572 480"
            fill="none" stroke="var(--ocean-pale)" stroke-width="14" stroke-linecap="round"/>
      <path class="middle-wave-shade" d="M250 345 C 275 365, 285 380, 292 395" fill="none" stroke="#e6e6e6" stroke-width="3"/>
      <path class="middle-wave-shade" d="M360 455 C 400 468, 430 472, 470 475" fill="none" stroke="#e6e6e6" stroke-width="3"/>
      <path class="foot-band" d="M0 640 C 170 720, 400 700, 572 600 L572 740 L0 740 Z" fill="url(#oceanFill)"/>
      <path class="foot-stripe" d="M0 628 C 170 706, 400 688, 572 588 L572 600 C 400 700, 170 720, 0 640 Z" fill="var(--silver)"/>
      <path class="foot-edge" d="M0 618 C 170 696, 400 678, 572 578" fill="none" stroke="var(--ocean)" stroke-width="1.5"/>
    </svg>

    <header class="brand">
      <span class="brand-dot"></span>
      <span class="brand-name">Tidewater Gardens</span>
    </header>

    <ul class="contact">
      <li><span class="icon"></span>410 Palm Cove Drive, Suite 200,</li>
      <li class="indent">Naples, FL 34102</li>
      <li><span class="icon"></span>(239) 555-0148 &nbsp;<span class="icon"></span>(239) 555-0193</li>
      <li><span class="icon"></span>hello@tidewatergardens.com</li>
      <li><span class="icon"></span>www.tidewatergardens.com</li>
    </ul>
  </section>
</main>
</body>
</html>
```